Laser Tattoo Removal Business Cards

We are looking for a professional business card design for a laser tattoo removal business. Ideally looking for a black business card design. The name of the business is Brightline Tattoo Removal. We place our cards at local tattoo shops so we ideally are looking for something trendy/edgy to draw both male and female clientele in.

Target Market(s)

Male/Female ages 18-60

Contact Information for Business Card

black background ideally.. hoping to stay within greys, whites and black

Font styles to use
Serif
Sans Serif

Colors
121212
a9a9a9
5c5c5c
f5f5f5
ffffff
7f7f7f
606060
848484
9d9d9d

Requirements
Must have
• Employee Info:
• Melissa Thornbury
• Chief Executive Offer
• m: 919.537.2846
• w: 919.362.4178
• f: 919.685.3907
• mthornbury@brightlinetattooremoval.example
• Address:
• 4615 Oakmere Pkwy, Suite 210
• Raleigh, NC 27654
• Website:
• www.brightlinetattooremoval.example
Nice to have
• Myabe business name on back or logo on back and employee info on the front

```html
<!DOCTYPE html>
<html lang="en">
<head>
<meta charset="utf-8">
<title>Brightline Tattoo Removal – Business Card</title>
<link rel="stylesheet" href="https://fonts.googleapis.com/css2?family=Oswald:wght@300;400&family=Montserrat:wght@400;600;700&family=Roboto+Condensed:wght@400&display=swap">
<style>
  :root {
    --ink: #121212;
    --band: #1d1c1a;
    --stage: #b4b4b4;
    --paper: #f5f5f5;
    --white: #ffffff;
    --grey-dark: #5c5c5c;
    --grey-mid: #7f7f7f;
    --grey-soft: #9d9d9d;
    --grey-light: #a9a9a9;
    --foil: #c8b36a;
  }
  * { margin: 0; padding: 0; box-sizing: border-box; }
  html, body { width: 1200px; height: 960px; overflow: hidden; }
  body {
    position: relative;
    background: var(--stage);
    font-family: "Montserrat", Arial, sans-serif;
  }
  .card { position: absolute; width: 600px; height: 343px; overflow: hidden; }

  /* Front */
  .card-front { left: 302px; top: 122px; }
  .card-front .paper-pattern {
    position: absolute; inset: 0;
    background: radial-gradient(circle at 50% 50%, var(--white) 0%, #f0f0f0 100%);
  }
  .brand-band {
    position: absolute; left: 0; top: 79px; width: 239px; height: 186px;
    background: var(--band);
    display: flex; align-items: center; justify-content: center;
  }
  .band-stub {
    position: absolute; left: 573px; top: 79px; width: 27px; height: 186px;
    background: var(--band);
  }
  .brand-name {
    font-family: "Oswald", Arial, sans-serif;
    font-weight: 400;
    text-transform: uppercase;
    text-align: center;
    letter-spacing: 2px;
    line-height: 1.25;
  }
  .brand-band .brand-name { color: var(--white); font-size: 22px; }

  .employee { position: absolute; left: 275px; top: 84px; color: var(--band); }
  .employee-name {
    font-family: "Oswald", Arial, sans-serif;
    font-weight: 400; font-size: 39px; line-height: 42px;
    text-transform: uppercase; letter-spacing: -0.5px;
    transform: scaleX(0.82); transform-origin: left;
  }
  .employee-title {
    font-size: 13px; font-weight: 600; color: var(--grey-soft);
    text-transform: uppercase; letter-spacing: 0.3px; line-height: 17px;
  }
  .employee-email {
    font-family: "Roboto Condensed", Arial, sans-serif;
    font-size: 14px; color: var(--grey-mid); line-height: 17px;
  }
  .contact { position: absolute; top: 175px; font-size: 13px; color: var(--grey-dark); line-height: 18px; }
  .phones { left: 275px; }
  .address { left: 420px; top: 177px; }
  .divider { position: absolute; left: 404px; top: 176px; width: 1px; height: 52px; background: var(--grey-dark); }
  .website {
    position: absolute; left: 275px; top: 246px;
    font-size: 13px; color: var(--grey-dark); letter-spacing: 0.2px;
  }
  .website strong { font-weight: 700; }

  /* Back */
  .card-back { left: 299px; top: 495px; }
  .card-back .paper-pattern {
    position: absolute; inset: 0;
    background: radial-gradient(circle at 50% 45%, #262626 0%, var(--band) 70%, #161616 100%);
  }
  .card-back .brand-name {
    position: absolute; left: 0; right: 0; top: 115px;
    color: var(--foil); font-size: 44px; letter-spacing: 4px;
  }
</style>
</head>
<body>
  <section class="card card-front" aria-label="Business card front">
    <div class="paper-pattern" role="img" aria-label="Light grey damask pattern on white card stock"></div>
    <div class="brand-band">
      <div class="brand-name">Brightline<br>Tattoo Removal</div>
    </div>
    <div class="band-stub"></div>

    <div class="employee">
      <div class="employee-name">Melissa Thornbury</div>
      <div class="employee-title">Chief Executive Offer</div>
      <div class="employee-email">mthornbury@brightlinetattooremoval.example</div>
    </div>

    <div class="contact phones">
      919.537.2846 (m)<br>
      919.362.4178 (w)<br>
      919.685.3907 (f)
    </div>
    <div class="divider"></div>
    <div class="contact address">
      4615 Oakmere Pkwy<br>
      Suite 210<br>
      Raleigh, NC 27654
    </div>

    <div class="website"><strong>BRIGHTLINETATTOOREMOVAL</strong>.example</div>
  </section>

  <section class="card card-back" aria-label="Business card back">
    <div class="paper-pattern" role="img" aria-label="Dark charcoal damask pattern on black card stock"></div>
    <div class="brand-name">Brightline<br>Tattoo Removal</div>
  </section>
</body>
</html>
```